Redesign of business card for Cedar Ridge Mechanical

We are looking for a new design for our business cards for Cedar Ridge Mechanical. We are a plumbing & HVAC construction company, operating on the West Coast of Canada and USA. Logo attached.
Industry/Entity Type
Construction - Plumbing & HVAC
Contact Information for Business Card
Name, address, phone numbers, email, website address
Look and feel
Each slider illustrates characteristics of the customer's brand and the style your logo design should communicate.

```html
<!DOCTYPE html>
<html lang="en">
<head>
<meta charset="utf-8">
<title>Cedar Ridge Mechanical – Business Card</title>
<link href="https://fonts.googleapis.com/css2?family=Poppins:wght@400;700&display=swap" rel="stylesheet">
<style>
  :root {
    --page-bg: #ffffff;
    --card-base: #141414;
    --disc: #181818;
    --disc-edge: #0c0c0c;
    --texture-dark: #262626;
    --texture-light: #c4c4c4;
    --ink: #ffffff;
    --icon-ink: #141414;
  }
  * { margin: 0; padding: 0; box-sizing: border-box; }
  html, body {
    width: 1200px; height: 1000px; overflow: hidden;
    background: var(--page-bg);
    font-family: "Poppins", sans-serif;
    color: var(--ink);
  }
  .canvas { position: relative; width: 1200px; height: 1000px; }
  .card {
    position: absolute; top: 110px;
    width: 478px; height: 779px;
    border-radius: 22px; overflow: hidden;
    background: var(--card-base);
  }
  .card--front { left: 115px; }
  .card--back { left: 607px; }
  .card__art { position: absolute; inset: 0; }
  .wordmark {
    position: absolute;
    display: flex; align-items: center; gap: 10px;
    font-weight: 700; color: var(--ink);
    white-space: nowrap;
  }
  .wordmark__square { width: 16px; height: 16px; background: var(--ink); flex: none; }
  .card--front .wordmark { left: 180px; top: 385px; transform: translateX(-50%); font-size: 21px; }
  .card--back .wordmark { left: 180px; top: 190px; transform: translateX(-50%); font-size: 19px; }
  .details {
    position: absolute; left: 0; width: 360px; top: 280px;
    text-align: center;
  }
  .details__name { font-weight: 700; font-size: 29px; line-height: 1.2; letter-spacing: 0.3px; }
  .details__title { font-size: 18px; margin-top: 2px; }
  .divider {
    display: flex; align-items: center; justify-content: center; gap: 6px;
    margin: 28px auto 0; width: 268px;
  }
  .divider__line { flex: 1; height: 1px; background: var(--ink); }
  .divider__icons { display: flex; gap: 5px; padding: 0 8px; }
  .icon-box {
    width: 24px; height: 24px; background: var(--ink);
    display: flex; align-items: center; justify-content: center;
  }
  .icon-box svg { width: 16px; height: 16px; }
  .contact { list-style: none; margin-top: 25px; font-size: 17.5px; line-height: 1.2; }
  .contact li { margin-bottom: 19px; }
  .contact .contact__address { line-height: 28px; margin-top: -2px; }
</style>
</head>
<body>
<main class="canvas">

  <section class="card card--front">
    <svg class="card__art" viewBox="0 0 478 779" width="478" height="779">
      <defs>
        <linearGradient id="textureFront" x1="0" x2="1" y1="0" y2="0">
          <stop offset="0.45" stop-color="var(--texture-dark)"/>
          <stop offset="1" stop-color="var(--texture-light)"/>
        </linearGradient>
        <radialGradient id="discFront" cx="0.5" cy="0.5" r="0.5">
          <stop offset="0.9" stop-color="var(--disc)"/>
          <stop offset="1" stop-color="var(--disc-edge)"/>
        </radialGradient>
      </defs>
      <rect x="150" y="8" width="320" height="763" rx="14" fill="url(#textureFront)" role="img" aria-label="Halftone dot texture fading from dark to light grey"/>
      <circle cx="-6" cy="390" r="418" fill="var(--disc-edge)" opacity="0.6"/>
      <circle cx="-6" cy="390" r="410" fill="url(#discFront)"/>
    </svg>
    <div class="wordmark"><span class="wordmark__square"></span>Cedar Ridge Mechanical</div>
  </section>

  <section class="card card--back">
    <svg class="card__art" viewBox="0 0 478 779" width="478" height="779">
      <defs>
        <linearGradient id="textureBack" x1="0" x2="1" y1="0" y2="0">
          <stop offset="0.45" stop-color="var(--texture-dark)"/>
          <stop offset="1" stop-color="var(--texture-light)"/>
        </linearGradient>
        <radialGradient id="discBack" cx="0.5" cy="0.5" r="0.5">
          <stop offset="0.9" stop-color="var(--disc)"/>
          <stop offset="1" stop-color="var(--disc-edge)"/>
        </radialGradient>
      </defs>
      <rect x="150" y="8" width="320" height="763" rx="14" fill="url(#textureBack)" role="img" aria-label="Halftone dot texture fading from dark to light grey"/>
      <circle cx="-6" cy="390" r="418" fill="var(--disc-edge)" opacity="0.6"/>
      <circle cx="-6" cy="390" r="410" fill="url(#discBack)"/>
    </svg>

    <div class="wordmark"><span class="wordmark__square"></span>Cedar Ridge Mechanical</div>

    <div class="details">
      <h1 class="details__name">Daniel Reeves</h1>
      <p class="details__title">Managing Director</p>

      <div class="divider">
        <span class="divider__line"></span>
        <div class="divider__icons">
          <span class="icon-box" aria-label="Phone">
            <svg viewBox="0 0 16 16"><path d="M2 6c0-2 2-3 6-3s6 1 6 3v1h-3V5.5H5V7H2z M4 8h8l1 5H3z" fill="var(--icon-ink)"/><circle cx="8" cy="10.5" r="1.4" fill="#fff"/></svg>
          </span>
          <span class="icon-box" aria-label="Email">
            <svg viewBox="0 0 16 16"><rect x="1.5" y="3.5" width="13" height="9" fill="var(--icon-ink)"/><path d="M1.5 3.5 8 9l6.5-5.5" fill="none" stroke="#fff" stroke-width="1.2"/></svg>
          </span>
          <span class="icon-box" aria-label="Website">
            <svg viewBox="0 0 16 16"><circle cx="8" cy="8" r="6.2" fill="none" stroke="var(--icon-ink)" stroke-width="1.3"/><ellipse cx="8" cy="8" rx="2.6" ry="6.2" fill="none" stroke="var(--icon-ink)" stroke-width="1.1"/><path d="M2 8h12M3 5h10M3 11h10" stroke="var(--icon-ink)" stroke-width="1"/></svg>
          </span>
          <span class="icon-box" aria-label="Address">
            <svg viewBox="0 0 16 16"><path d="M8 1.5a4.5 4.5 0 0 1 4.5 4.5c0 3.4-4.5 8.5-4.5 8.5S3.5 9.4 3.5 6A4.5 4.5 0 0 1 8 1.5z" fill="var(--icon-ink)"/><circle cx="8" cy="6" r="1.7" fill="#fff"/></svg>
          </span>
        </div>
        <span class="divider__line"></span>
      </div>

      <ul class="contact">
        <li>044-555 210 347</li>
        <li>info@cedarridge.com</li>
        <li>www.cedarridgemech.com</li>
        <li class="contact__address">Unit 12 480 Harbour Lane Crescent,<br>North Alderview, BC V5K 2R1</li>
      </ul>
    </div>
  </section>

</main>
</body>
</html>
```